Design a Mobile App for Landscape Businesses

This project is to design the first three screens for a mobile app for Landscape and Lawncare businesses. This app will serve as a directory for homeowners to locate landscape and lawn care businesses and for landscape businesses and contractors to run their business. See the attached PDF for more information and example
Here is the link to the description https://lnkbrev.example/q7z3Kp

Target Market(s)

Landscape and lawn care business, gardeners, home owners

Industry/Entity Type

Landscape Gardening

Logo Text

Verdalink

Colors

Designer to choose colors to be used in the design.

```html
<!DOCTYPE html>
<html lang="en">
<head>
<meta charset="utf-8">
<title>Verdalink – Find a Gardener</title>
<link href="https://fonts.googleapis.com/css2?family=Montserrat:wght@500;600;700&family=Open+Sans:wght@400;600&display=swap" rel="stylesheet">
<style>
:root{
  --teal:#2cb4d6;
  --ink:#1e2838;
  --body:#555d66;
  --muted:#8a9096;
  --line:#e3e6e8;
  --bg:#eef1f3;
  --white:#ffffff;
  --alert:#f26a21;
}
*{box-sizing:border-box;margin:0;padding:0}
html,body{width:675px;height:1200px;overflow:hidden;background:var(--white)}
body{font-family:"Open Sans",Arial,sans-serif;position:relative;color:var(--ink)}
.status-bar{position:absolute;top:0;left:0;width:675px;height:43px;display:flex;justify-content:flex-end;align-items:center;gap:10px;padding-right:18px;font-family:"Montserrat",sans-serif;font-size:20px;font-weight:500;color:#333}
.app-header{position:absolute;top:43px;left:0;width:675px;height:83px;display:flex;align-items:center;padding:0 27px;border-bottom:2px solid var(--line)}
.app-title{font-family:"Montserrat",sans-serif;font-weight:700;font-size:27px;flex:1}
.header-link{font-family:"Montserrat",sans-serif;font-weight:600;font-size:25px;color:var(--teal);margin-left:40px}
.filter-bar{position:absolute;top:126px;left:0;width:675px;height:90px;display:flex;border-bottom:2px solid var(--line)}
.filter{flex:1;display:flex;align-items:center;padding:0 22px;gap:12px;font-family:"Montserrat",sans-serif;font-size:22px;color:var(--ink)}
.filter + .filter{border-left:2px solid var(--line)}
.filter strong{font-weight:700}
.filter .chev{margin-left:auto}
.listing-area{position:absolute;top:216px;left:0;width:675px;height:904px;background:var(--bg)}
.card{position:absolute;left:0;width:675px;background:var(--white)}
.card-one{top:5px;height:567px}
.card-two{top:589px;height:330px}
.card-photo{position:absolute;left:0;top:0;width:675px;height:355px;background:linear-gradient(180deg,#9fb0bc 0%,#8a5a4a 35%,#4f6f3a 70%,#3d5a2c 100%)}
.card-two .card-photo{background:linear-gradient(180deg,#c9dbe8 0%,#b9bdb8 40%,#7d8f63 80%,#5f7446 100%)}
.tags{position:absolute;left:20px;top:288px;display:flex;gap:12px}
.tag{display:flex;align-items:center;gap:6px;height:47px;padding:0 18px 0 14px;border:2px solid var(--white);border-radius:24px;color:var(--white);font-size:20px;background:rgba(0,0,0,.12)}
.card-name{position:absolute;left:27px;top:385px;font-family:"Montserrat",sans-serif;font-weight:700;font-size:29px;color:var(--ink)}
.card-desc{position:absolute;left:27px;top:434px;width:510px;font-size:21px;line-height:32px;color:var(--body)}
.card-quote{position:absolute;right:18px;top:448px;display:flex;align-items:center;gap:6px;font-family:"Montserrat",sans-serif;font-weight:600;font-size:22px;color:var(--teal)}
.card-phone{position:absolute;left:27px;top:513px;display:flex;align-items:center;gap:12px;font-size:23px;color:var(--ink)}
.tab-bar{position:absolute;top:1120px;left:0;width:675px;height:80px;background:var(--white);border-top:2px solid var(--line);display:flex}
.tab{flex:1;display:flex;flex-direction:column;align-items:center;justify-content:center;gap:6px;font-family:"Montserrat",sans-serif;font-size:18px;color:var(--muted)}
.tab.active{color:var(--teal);font-weight:600}
.tab-icon{position:relative}
.badge{position:absolute;top:-3px;right:-6px;width:13px;height:13px;border-radius:50%;background:var(--alert)}
</style>
</head>
<body>
<div class="status-bar">
  <svg width="20" height="20" viewBox="0 0 20 20"><circle cx="10" cy="11" r="7" fill="none" stroke="#333" stroke-width="2"/><path d="M10 7v4l3 2" stroke="#333" stroke-width="2" fill="none"/></svg>
  <svg width="22" height="18" viewBox="0 0 22 18"><path d="M11 17L0 4a16 16 0 0 1 22 0z" fill="#333"/></svg>
  <svg width="18" height="18" viewBox="0 0 18 18"><path d="M18 0v18H0z" fill="#333"/></svg>
  <svg width="12" height="20" viewBox="0 0 12 20"><rect x="3" y="0" width="6" height="2" fill="#333"/><rect x="0" y="2" width="12" height="18" rx="1" fill="#333"/></svg>
  <span>16:54</span>
</div>

<header class="app-header">
  <h1 class="app-title">Find a Gardener</h1>
  <span class="header-link">Filter</span>
  <span class="header-link">Map</span>
</header>

<div class="filter-bar">
  <div class="filter">
    <svg width="18" height="26" viewBox="0 0 18 26"><path d="M9 0a9 9 0 0 1 9 9c0 7-9 17-9 17S0 16 0 9a9 9 0 0 1 9-9z" fill="var(--teal)"/><circle cx="9" cy="9" r="3.5" fill="#fff"/></svg>
    <strong>Current Location</strong>
    <svg class="chev" width="20" height="12" viewBox="0 0 20 12"><path d="M2 2l8 8 8-8" stroke="#333" stroke-width="2.2" fill="none"/></svg>
  </div>
  <div class="filter">
    <svg width="26" height="26" viewBox="0 0 26 26"><circle cx="13" cy="13" r="11" fill="none" stroke="var(--teal)" stroke-width="2.4"/><path d="M13 7v7h5" stroke="var(--teal)" stroke-width="2.4" fill="none"/></svg>
    <span>Available: <strong>Anytime</strong></span>
    <svg class="chev" width="20" height="12" viewBox="0 0 20 12"><path d="M2 2l8 8 8-8" stroke="#333" stroke-width="2.2" fill="none"/></svg>
  </div>
</div>

<main class="listing-area">
  <article class="card card-one">
    <div class="card-photo" role="img" aria-label="Photo of a brick house with a terraced stone-wall garden, shrubs and a red-leaved tree"></div>
    <div class="tags">
      <span class="tag"><svg width="12" height="18" viewBox="0 0 18 26"><path d="M9 0a9 9 0 0 1 9 9c0 7-9 17-9 17S0 16 0 9a9 9 0 0 1 9-9z" fill="#fff"/></svg>Scarborough</span>
      <span class="tag"><svg width="12" height="18" viewBox="0 0 18 26"><path d="M9 0a9 9 0 0 1 9 9c0 7-9 17-9 17S0 16 0 9a9 9 0 0 1 9-9z" fill="#fff"/></svg>Whitby</span>
      <span class="tag"><svg width="12" height="18" viewBox="0 0 18 26"><path d="M9 0a9 9 0 0 1 9 9c0 7-9 17-9 17S0 16 0 9a9 9 0 0 1 9-9z" fill="#fff"/></svg>Filey</span>
    </div>
    <h2 class="card-name">Harold’s Groundworks</h2>
    <p class="card-desc">Experienced and skilled gardener based in Scarborough. I specialise in law care, hedge…</p>
    <span class="card-quote">Quote <svg width="14" height="24" viewBox="0 0 14 24"><path d="M2 2l10 10-10 10" stroke="var(--teal)" stroke-width="2.6" fill="none"/></svg></span>
    <div class="card-phone">
      <svg width="16" height="26" viewBox="0 0 16 26"><rect x="1.2" y="1.2" width="13.6" height="23.6" rx="2.5" fill="none" stroke="var(--teal)" stroke-width="2.4"/><line x1="6" y1="20.5" x2="10" y2="20.5" stroke="var(--teal)" stroke-width="2"/></svg>
      07000 318 642
    </div>
  </article>

  <article class="card card-two">
    <div class="card-photo" role="img" aria-label="Photo of a white single-storey house with a lawn, trees and a pool"></div>
    <div class="tags">
      <span class="tag"><svg width="12" height="18" viewBox="0 0 18 26"><path d="M9 0a9 9 0 0 1 9 9c0 7-9 17-9 17S0 16 0 9a9 9 0 0 1 9-9z" fill="#fff"/></svg>Scarborough</span>
      <span class="tag"><svg width="12" height="18" viewBox="0 0 18 26"><path d="M9 0a9 9 0 0 1 9 9c0 7-9 17-9 17S0 16 0 9a9 9 0 0 1 9-9z" fill="#fff"/></svg>Whitby</span>
      <span class="tag"><svg width="12" height="18" viewBox="0 0 18 26"><path d="M9 0a9 9 0 0 1 9 9c0 7-9 17-9 17S0 16 0 9a9 9 0 0 1 9-9z" fill="#fff"/></svg>Filey</span>
    </div>
  </article>
</main>

<nav class="tab-bar">
  <div class="tab active">
    <svg class="tab-icon" width="34" height="32" viewBox="0 0 34 32"><path d="M13 1a10 10 0 0 1 10 10c0 8-10 19-10 19S3 19 3 11A10 10 0 0 1 13 1z" fill="none" stroke="var(--teal)" stroke-width="2.6"/><circle cx="13" cy="11" r="4" fill="var(--teal)"/><circle cx="25" cy="23" r="5" fill="none" stroke="var(--teal)" stroke-width="2.4"/><line x1="28.5" y1="26.5" x2="32" y2="30" stroke="var(--teal)" stroke-width="2.6"/></svg>
    Search
  </div>
  <div class="tab">
    <svg width="30" height="28" viewBox="0 0 30 28"><g stroke="var(--muted)" stroke-width="2.2"><line x1="1" y1="4" x2="7" y2="4"/><line x1="11" y1="4" x2="29" y2="4"/><line x1="1" y1="14" x2="7" y2="14"/><line x1="11" y1="14" x2="29" y2="14"/><line x1="1" y1="24" x2="7" y2="24"/><line x1="11" y1="24" x2="29" y2="24"/></g></svg>
    Bookings
  </div>
  <div class="tab">
    <span class="tab-icon"><svg width="34" height="26" viewBox="0 0 34 26"><rect x="1.2" y="1.2" width="31.6" height="23.6" rx="2" fill="none" stroke="var(--muted)" stroke-width="2.2"/><path d="M2 3l15 12L32 3" fill="none" stroke="var(--muted)" stroke-width="2.2"/></svg><span class="badge"></span></span>
    Messages
  </div>
  <div class="tab">
    <svg width="30" height="30" viewBox="0 0 30 30"><g fill="none" stroke="var(--muted)" stroke-width="2.2"><circle cx="15" cy="15" r="5"/><path d="M13 2h4l1 4 3 1.5 3.5-2 3 3-2 3.5L27 15l-2.5 3.5 2 3.5-3 3-3.5-2L17 24.5 16 28h-4l-1-3.5L8 23l-3.5 2-3-3 2-3.5L2 15l1.5-3.5-2-3.5 3-3 3.5 2L11 6z"/></g></svg>
    Account
  </div>
</nav>
</body>
</html>
```